Pet sitting Business needs a website

We need a website that shows our services and prices. Shows our love of animals but also our professionalism. want a gallery, about, blog, services, links to fb and instagram accounts, newsletter archive. want it to be easy to access and wonderful to navigate. want the domain to be Birchfordpawhaven.com
take any info from FB site www.facebook.com/birchfordpawhaven
I would like it to fit square space platform

Target Market(s)

upscale area, responsible pet owners,

Industry/Entity Type

Pet Care

Coding

Coded - Design and coding required

Number of Pages Required

5+ page

Font styles to use
Sans Serif

Requirements
Must have
• (square space platform)
• Menu
• photo gallery
• about us
• services
• policies
• monthly newsletter
• unavailable dates
• Introduction (welcome)
• payment methods
• Daily updates
• testimonials (use from fb site)
Should not have
• stock photos

```html
<!DOCTYPE html>
<html lang="en">
<head>
<meta charset="utf-8">
<title>Birchford Paw Haven – Petsitting Club</title>
<link href="https://fonts.googleapis.com/css2?family=Roboto:wght@300;400;500;700&family=Open+Sans:wght@400;600&display=swap" rel="stylesheet">
<style>
:root{
  --gold:#dc9a07;
  --gold-dark:#c98a00;
  --blue:#0a8fc2;
  --blue-dark:#0779a6;
  --navy:#1d3a52;
  --ink:#222;
  --muted:#666;
  --light:#f1f1f1;
  --footer:#2b2b2b;
  --footer-deep:#1c1c1c;
  --white:#fff;
}
*{margin:0;padding:0;box-sizing:border-box}
html,body{width:1200px;height:2866px;overflow:hidden}
body{font-family:'Roboto',Arial,sans-serif;color:var(--ink);background:var(--white);position:relative}
a{text-decoration:none;color:inherit}

.topline{position:absolute;left:0;top:0;width:1200px;height:4px;background:linear-gradient(90deg,#5a4a1a,var(--gold),#5a4a1a)}
.header{position:absolute;top:4px;left:0;width:1200px;height:149px}
.contact-strip{position:absolute;left:97px;top:66px;display:flex;gap:30px;font-size:12px;color:var(--muted)}
.contact-strip span{display:flex;align-items:center;gap:8px}
.contact-strip svg{width:12px;height:12px;fill:var(--blue)}
.brand{position:absolute;left:450px;top:40px;width:300px;text-align:center}
.brand-mark{display:inline-block;width:14px;height:14px;border-radius:50%;background:var(--gold);vertical-align:middle;margin-right:8px}
.brand-name{font-size:28px;font-weight:500;color:var(--gold);vertical-align:middle}
.brand-sub{font-size:11px;color:var(--blue-dark);letter-spacing:3px;margin-top:4px}
.social{position:absolute;right:96px;top:58px;display:flex;gap:14px}
.social span{width:38px;height:38px;border:1px solid #333;border-radius:50%}

.nav{position:absolute;top:153px;left:0;width:1200px;height:53px;background:linear-gradient(var(--blue),var(--blue-dark));display:flex;padding-left:97px}
.nav a{color:var(--white);font-size:14px;line-height:53px;padding:0 17px}
.nav a.active{background:var(--gold);padding:0 28px}

.hero{position:absolute;top:206px;left:0;width:1200px;height:497px;background:linear-gradient(160deg,#3c5a6e,#21394d 55%,#17293a)}
.hero-title{position:absolute;top:150px;width:100%;text-align:center;color:var(--white);font-size:50px;font-weight:700;letter-spacing:1px}
.hero-sub{position:absolute;top:214px;width:100%;text-align:center;color:#e6eef3;font-size:27px;font-weight:300}
.hero-btn{position:absolute;left:535px;top:287px;width:128px;height:42px;border:1px solid var(--white);color:var(--white);font-size:16px;line-height:40px;text-align:center}
.hero-arrow{position:absolute;top:233px;width:34px;height:34px;border:1px solid #9fb3c1;border-radius:50%}
.hero-arrow svg{width:100%;height:100%;stroke:#cfd9e0;fill:none;stroke-width:2}

.service{position:absolute;top:640px;width:220px;text-align:center}
.service-photo{width:204px;height:165px;margin:0 auto;border-radius:102px 102px 0 0;border:5px solid var(--white);border-bottom:none;box-shadow:0 -2px 4px rgba(0,0,0,.15)}
.service-name{margin-top:22px;font-size:21px;font-weight:500}
.service-price{margin-top:6px;color:var(--gold);font-size:24px;font-weight:700}
.service-price small{font-size:10px;font-weight:400;margin-left:4px}
.service-note{font-family:'Open Sans',sans-serif;font-size:11px;color:var(--muted);line-height:23px;margin-top:4px}
.service-more{display:block;margin-top:8px;color:var(--gold);font-size:13px}

.why{position:absolute;top:1007px;left:0;width:1200px;height:526px;background:var(--light)}
.section-title{position:absolute;width:100%;text-align:center;font-size:26px;font-weight:500;color:var(--ink)}
.rule{position:absolute;left:578px;width:44px;height:2px;background:var(--blue)}
.why-intro{position:absolute;top:117px;left:235px;width:730px;text-align:center;font-family:'Open Sans',sans-serif;font-size:11px;line-height:23px;color:var(--muted)}
.feature{position:absolute;top:186px;width:300px;text-align:center}
.feature-icon{width:126px;height:126px;border-radius:50%;background:var(--gold);margin:0 auto}
.feature-name{margin-top:36px;font-size:17px;color:#333}
.feature-text{margin-top:12px;font-family:'Open Sans',sans-serif;font-size:11px;line-height:21px;color:var(--muted)}
.feature-btn{display:inline-block;margin-top:14px;width:96px;height:35px;background:var(--gold);color:var(--white);font-size:13px;font-weight:500;line-height:35px}

.gallery{position:absolute;top:1533px;left:0;width:1200px;height:525px;display:grid;grid-template-columns:repeat(4,1fr);grid-template-rows:repeat(2,1fr);gap:2px;background:#fff}
.gallery div{width:100%;height:100%}

.testimonials{position:absolute;top:2058px;left:0;width:1200px;height:369px;background:#fafafa}
.avatar{position:absolute;top:126px;width:73px;height:73px;border-radius:50%;border:3px solid #ddd;background:linear-gradient(#c9b2a0,#8a6f5d)}
.quote{position:absolute;top:140px;width:369px;height:172px;border:2px solid var(--gold);background:var(--white)}
.quote::before{content:"";position:absolute;left:-12px;top:18px;border:10px solid transparent;border-right-color:var(--gold);border-left:none}
.quote p{padding:18px 20px 0;font-family:'Open Sans',sans-serif;font-size:12px;line-height:20px;color:var(--muted)}
.quote-foot{position:absolute;left:0;bottom:0;width:100%;height:63px;background:var(--gold);color:var(--white);padding:14px 20px}
.quote-foot b{display:block;font-size:13px;font-weight:500}
.quote-foot span{font-size:11px}

.newsletter{position:absolute;top:2427px;left:0;width:1200px;height:105px;background:#333}
.newsletter-band{position:absolute;left:0;top:0;width:669px;height:105px;background:var(--blue-dark);clip-path:polygon(0 0,587px 0,669px 100%,0 100%)}
.newsletter-band h3{position:absolute;left:190px;top:22px;color:var(--white);font-weight:500;font-size:21px;line-height:30px}
.newsletter-band h3 span{display:block;font-size:25px}
.newsletter-form{position:absolute;left:678px;top:40px;display:flex}
.newsletter-form .field{width:289px;height:36px;background:var(--white);font-size:12px;color:#777;line-height:36px;padding-left:42px}
.newsletter-form .submit{width:132px;height:36px;background:var(--gold);color:var(--white);font-size:14px;line-height:36px;text-align:center}

.footer{position:absolute;top:2532px;left:0;width:1200px;height:268px;background:var(--footer)}
.footer-col{position:absolute;top:56px}
.footer-col h4{color:var(--white);font-size:16px;font-weight:500;margin-bottom:16px}
.footer-col li{list-style:none;color:#a9a9a9;font-size:12px;line-height:26px}
.footer-col.links li::before{content:"»";margin-right:12px;color:#bbb}
.footer-col.contact li svg{width:11px;height:11px;fill:#bbb;margin-right:10px;vertical-align:-1px}
.copyright{position:absolute;top:2800px;left:0;width:1200px;height:66px;background:var(--footer-deep);color:#ddd;font-size:12px;text-align:center;line-height:66px}
</style>
</head>
<body>
<div class="topline"></div>

<header class="header">
  <div class="contact-strip">
    <span><svg viewBox="0 0 24 24"><path d="M6.6 10.8a15 15 0 006.6 6.6l2.2-2.2a1 1 0 011-.25 11.4 11.4 0 003.6.6 1 1 0 011 1V20a1 1 0 01-1 1A17 17 0 013 4a1 1 0 011-1h3.5a1 1 0 011 1c0 1.25.2 2.45.57 3.57a1 1 0 01-.25 1z"/></svg>+1 210 555 0148</span>
    <span><svg viewBox="0 0 24 24"><path d="M2 5h20v14H2zm2 2v.5l8 5 8-5V7z"/></svg>info@birchfordpawhaven.com</span>
  </div>
  <div class="brand">
    <span class="brand-mark"></span><span class="brand-name">Birchford Paw Haven</span>
    <div class="brand-sub">PETSITTING CLUB</div>
  </div>
  <div class="social"><span></span><span></span><span></span><span></span></div>
</header>

<nav class="nav">
  <a class="active">Home</a><a>About us</a><a>Services</a><a>Photo gallery</a><a>Policies</a><a>Monthly newsletter</a><a>Unavailable dates</a><a>Payment methods</a><a>Contact us</a>
</nav>

<section class="hero" role="img" aria-label="Photo of a dog relaxing outdoors, darkened blue tone">
  <div class="hero-arrow" style="left:25px"><svg viewBox="0 0 34 34"><path d="M19 11l-6 6 6 6"/></svg></div>
  <div class="hero-arrow" style="right:25px"><svg viewBox="0 0 34 34"><path d="M15 11l6 6-6 6"/></svg></div>
  <h1 class="hero-title">WE ARE BIRCHFORD PAW HAVEN</h1>
  <p class="hero-sub">Petsitting Club headed by Lic. Mara Dell</p>
  <a class="hero-btn">Learn More</a>
</section>

<div class="service" style="left:94px">
  <div class="service-photo" role="img" aria-label="Dog on a leash in a green garden" style="background:linear-gradient(#5d7a3f,#8ea46a)"></div>
  <div class="service-name">Daily Visit</div>
  <div class="service-price">$25.00<small>/ (per visit)</small></div>
  <div class="service-note">No additional charge for each pet<br>Dog walks or play time</div>
  <a class="service-more">Read More</a>
</div>
<div class="service" style="left:356px">
  <div class="service-photo" role="img" aria-label="Cat on a wooden railing" style="background:linear-gradient(#b8a58f,#5a4a46)"></div>
  <div class="service-name">Potty visits</div>
  <div class="service-price">$10.00</div>
  <div class="service-note">No additional charge for each pet<br>Dog walks or play time</div>
  <a class="service-more">Read More</a>
</div>
<div class="service" style="left:618px">
  <div class="service-photo" role="img" aria-label="Pet inside a travel crate" style="background:linear-gradient(#4a3a30,#7a5a3d)"></div>
  <div class="service-name">Pet Taxi</div>
  <div class="service-price">$10.00<small>(each trip)</small></div>
  <div class="service-note">No additional charge for each pet<br>Dog walks or play time</div>
  <a class="service-more">Read More</a>
</div>
<div class="service" style="left:882px">
  <div class="service-photo" role="img" aria-label="Cat beside a food bowl" style="background:linear-gradient(#9c8a78,#3f5a5e)"></div>
  <div class="service-name">Medication</div>
  <div class="service-price">$5.00<small>/ (per Admition)</small></div>
  <div class="service-note">No additional charge for each pet<br>Dog walks or play time</div>
  <a class="service-more">Read More</a>
</div>

<section class="why">
  <h2 class="section-title" style="top:46px">Why Choose Us</h2>
  <div class="rule" style="top:96px"></div>
  <p class="why-intro">It is a long established fact that a reader will be distracted by the readable content of a page when looking at its layout. The point of using Lorem Ipsum is that it has a more-or-less normal distribution of letters, as opposed to using 'Content here, content here</p>
  <div class="feature" style="left:127px">
    <div class="feature-icon" role="img" aria-label="Dog symbol"></div>
    <div class="feature-name">Finibus Bonorum et</div>
    <p class="feature-text">The standard chunk of Lorem Ipsum used since the<br>is reproduced below for those interested.</p>
    <a class="feature-btn">Read More</a>
  </div>
  <div class="feature" style="left:448px">
    <div class="feature-icon" role="img" aria-label="Dog and cat symbol"></div>
    <div class="feature-name">Finibus Bonorum et</div>
    <p class="feature-text">The standard chunk of Lorem Ipsum used since the<br>is reproduced below for those interested.</p>
    <a class="feature-btn">Read More</a>
  </div>
  <div class="feature" style="left:773px">
    <div class="feature-icon" role="img" aria-label="Paw award ribbon symbol"></div>
    <div class="feature-name">Finibus Bonorum et</div>
    <p class="feature-text">The standard chunk of Lorem Ipsum used since the<br>is reproduced below for those interested.</p>
    <a class="feature-btn">Read More</a>
  </div>
</section>

<section class="gallery">
  <div role="img" aria-label="Tortoises on the ground" style="background:linear-gradient(135deg,#5b4636,#2f2520)"></div>
  <div role="img" aria-label="Girl holding a pug on the lawn" style="background:linear-gradient(135deg,#4e6b35,#8a9a78)"></div>
  <div role="img" aria-label="Fluffy dog on a wooden floor" style="background:linear-gradient(135deg,#8a6a48,#c9b59a)"></div>
  <div role="img" aria-label="Woman hugging a black dog" style="background:linear-gradient(135deg,#3a3634,#7d6a5c)"></div>
  <div role="img" aria-label="Child lying with a small dog" style="background:linear-gradient(135deg,#9a8a7e,#5e4a3f)"></div>
  <div role="img" aria-label="Pug beside a pink flower" style="background:linear-gradient(135deg,#8d6f5a,#b8405e)"></div>
  <div role="img" aria-label="Child and dog playing in a backyard" style="background:linear-gradient(135deg,#2f3a2a,#5c6e3c)"></div>
  <div role="img" aria-label="Black and white cat in a basket" style="background:linear-gradient(135deg,#4a4038,#7a6c60)"></div>
</section>

<section class="testimonials">
  <h2 class="section-title" style="top:42px;font-size:24px">Our Client Testimonial</h2>
  <div class="rule" style="top:98px"></div>
  <div class="avatar" style="left:101px" role="img" aria-label="Client portrait"></div>
  <div class="quote" style="left:210px">
    <p>There are many variations of passages of Lorem Ipsum available, but the majority have suffered alteration in some form, by injected humour, or randomised words which don't look even slightly believable.</p>
    <div class="quote-foot"><b>John Doe</b><span>CEO, Company Name</span></div>
  </div>
  <div class="avatar" style="left:620px" role="img" aria-label="Client portrait"></div>
  <div class="quote" style="left:732px">
    <p>There are many variations of passages of Lorem Ipsum available, but the majority have suffered alteration in some form, by injected humour, or randomised words which don't look even slightly believable.</p>
    <div class="quote-foot"><b>John Doe</b><span>CEO, Company Name</span></div>
  </div>
</section>

<section class="newsletter">
  <div class="newsletter-band"><h3>SUBSCRIBE<span>TO OUR NEWSLETTER</span></h3></div>
  <div class="newsletter-form"><div class="field">Enter Your Email Address</div><div class="submit">Subscribe</div></div>
</section>

<footer class="footer">
  <div class="footer-col links" style="left:97px"><h4>QUICK LINKS</h4><ul><li>photo gallery</li><li>about us</li><li>services</li><li>policies</li><li>Contact us</li></ul></div>
  <div class="footer-col links" style="left:289px"><h4>RECENT POSTS</h4><ul><li>Finibus Bonorum</li><li>Randomised words</li><li>Anything embarrassing</li><li>Renaissance</li></ul></div>
  <div class="footer-col links" style="left:495px"><h4>USEFUL TIPS</h4><ul><li>Finibus Bonorum</li><li>Randomised words</li><li>Anything embarrassing</li><li>Renaissance</li><li>Anything embarrassing</li></ul></div>
  <div class="footer-col" style="left:720px"><h4>WORKING HOURS</h4><ul><li>Monday - Friday 10AM - 10PM</li><li>Saturday 9AM - 8PM</li><li>Sunday 9AM - 6PM</li></ul></div>
  <div class="footer-col contact" style="left:935px"><h4>CONTACT US</h4><ul>
    <li><svg viewBox="0 0 24 24"><path d="M12 3l10 9h-3v9h-5v-6h-4v6H5v-9H2z"/></svg>00 Latin words, combined</li>
    <li><svg viewBox="0 0 24 24"><path d="M6.6 10.8a15 15 0 006.6 6.6l2.2-2.2a1 1 0 011-.25 11.4 11.4 0 003.6.6 1 1 0 011 1V20a1 1 0 01-1 1A17 17 0 013 4a1 1 0 011-1h3.5a1 1 0 011 1c0 1.25.2 2.45.57 3.57a1 1 0 01-.25 1z"/></svg>2105550148 / 2105550149</li>
    <li><svg viewBox="0 0 24 24"><path d="M2 5h20v14H2zm2 2v.5l8 5 8-5V7z"/></svg>hello@birchfordpawhaven.com</li>
  </ul></div>
</footer>
<div class="copyright">Copyrights@2016 Birchfordpawhaven.com , All rights reserved</div>
</body>
</html>
```